Tri-fold flyer for our high quality fast-food concept

This is a project for a tri-fold flyer with the presentation and menu of our new takeaway and delivery high quality fast-food concept.

The whole flyer should look modern and high quality.

The vegetarian options should be notified by a little sign, like a leave for example.
Vegetarian options are:
Authentic, Veggie, Cheese, Malvenne, Tessala, Rima Dubel, Pelvo, Mursgrave, Vestal, Quelvira, Bellucave, Tarvik, Verte, Fries, Focaccia

The most specific products in our menu are the burgers, gnocchi and piozzas, if it is possible to slightly put in evidence these sections.

It would be nice if you could reuse the peppers of our logo in a subtle way.

In attachment are:
- a draft for the flyer indicating the position of each section, with the contents (dishes with ingredients and prices). PDF shows how it should look like, DOC might easier me to read the contents
- the logo which should be used at least in the front page
- some pictures of our dishes. One picture for each section would probably be nice.
- the QR Code on the back page (see yellow text)
- 2 pictures of the packaging as we use environmentally friendly ones (see yellow the in the back page).

Please note that this is a long term partnership, as we will work again with the winner when we will need to make small changes to our menu, so we hope you will provide us with a lovely and professional design :-)

Besoin de plus de jours pour examiner

Target Market(s)

Local people between 25-45

Industry/Entity Type

Fast food

Requirements
Must have
• It is much better if you could use the colors of our logo, to create a whole atmosphere
Nice to have
• Agood balance between bright and dark - Though there is much content, the text should not be too small

```html
<!DOCTYPE html>
<html lang="en">
<head>
<meta charset="utf-8">
<title>Malvenne – Trifold Restaurant Brochure</title>
<link href="https://fonts.googleapis.com/css2?family=Montserrat:wght@400;500;600;700&family=Pacifico&display=swap" rel="stylesheet">
<style>
  :root {
    --backdrop: #ffd60a;
    --sheet-dark: #2a2a2a;
    --sheet-mid: #313131;
    --sheet-fold: #262626;
    --accent: #ffd400;
    --ink-light: #f4f4f4;
    --ink-soft: #cfcfcf;
    --photo-warm-a: #6b4a2e;
    --photo-warm-b: #c98b4a;
    --photo-dark-a: #3a3632;
    --photo-dark-b: #5b4a3a;
  }
  * { box-sizing: border-box; margin: 0; padding: 0; }
  html, body {
    width: 1200px; height: 600px; overflow: hidden;
    background: var(--backdrop);
    font-family: "Montserrat", sans-serif;
  }
  .canvas { position: relative; width: 1200px; height: 600px; }

  .sheet {
    position: absolute; top: 143px;
    width: 502px; height: 355px;
    background: var(--sheet-dark);
    overflow: hidden;
  }
  .sheet--outside { left: 72px; }
  .sheet--inside { left: 627px; }

  .panel-shade {
    position: absolute; top: 0; height: 100%; width: 167px;
  }
  .panel-shade--a { left: 0; background: var(--sheet-dark); }
  .panel-shade--b { left: 167px; background: var(--sheet-mid); }
  .panel-shade--c { left: 334px; background: var(--sheet-fold); }

  .photo-layer { position: absolute; inset: 0; width: 100%; height: 100%; }

  .script-title {
    position: absolute;
    font-family: "Pacifico", cursive;
    color: var(--ink-light);
    font-weight: 400;
    line-height: 1.05;
  }
  .body-copy {
    position: absolute;
    font-size: 5.6px; line-height: 6.6px;
    color: var(--ink-soft);
  }
  .body-copy p + p { margin-top: 6px; }

  /* outside sheet */
  .about-title { left: 24px; top: 40px; font-size: 22px; }
  .about-copy { left: 25px; top: 78px; width: 120px; }
  .claim-title { left: 167px; width: 167px; top: 42px; font-size: 19px; text-align: center; }
  .claim-copy { left: 184px; top: 98px; width: 134px; text-align: center; }

  .brand {
    position: absolute; left: 387px; top: 26px;
    display: flex; align-items: center; gap: 4px;
    font-size: 8.5px; font-weight: 700; color: var(--ink-light);
    letter-spacing: 0.3px; text-transform: uppercase;
  }
  .brand-mark { width: 7px; height: 7px; background: var(--ink-light); }

  .cover-title { left: 360px; width: 142px; top: 62px; text-align: center; }
  .cover-title .line-small { display: block; font-size: 19px; }
  .cover-title .line-large { display: block; font-size: 27px; margin-top: 2px; }

  .website {
    position: absolute; left: 167px; width: 167px; top: 312px;
    text-align: center; font-size: 7.6px; color: var(--ink-light); letter-spacing: 0.3px;
  }
  .hours {
    position: absolute; left: 346px; width: 156px; top: 298px;
    text-align: center; font-size: 9.4px; font-weight: 600;
    color: var(--ink-light); line-height: 14px; letter-spacing: 0.3px;
  }

  /* inside sheet */
  .menu-title { top: 28px; font-size: 15px; }
  .menu-title--foods { left: 37px; }
  .menu-title--drinks { left: 207px; }

  .menu-column { position: absolute; top: 68px; width: 115px; }
  .menu-column--foods { left: 37px; }
  .menu-column--drinks { left: 207px; }

  .menu-group { height: 53px; }
  .menu-group h3 {
    font-size: 6.4px; font-weight: 700; color: var(--ink-light);
    letter-spacing: 0.3px; margin-bottom: 5px;
  }
  .menu-item {
    display: flex; justify-content: space-between;
    font-size: 4.6px; line-height: 9.2px; color: var(--ink-soft);
  }
  .menu-item .price { width: 16px; }

  .fold-line {
    position: absolute; top: 0; width: 1px; height: 100%;
    background: rgba(0,0,0,0.25);
  }
</style>
</head>
<body>
<main class="canvas">

  <!-- Outside sheet: about, claim, cover -->
  <section class="sheet sheet--outside">
    <div class="panel-shade panel-shade--a"></div>
    <div class="panel-shade panel-shade--b"></div>
    <div class="panel-shade panel-shade--c"></div>

    <svg class="photo-layer" viewBox="0 0 502 355" role="img" aria-label="Food photograph: fried chicken with lettuce and tomatoes on a wooden board, with bowls of peanuts, ketchup and fries">
      <defs>
        <linearGradient id="outsidePhoto" x1="0" y1="0" x2="1" y2="1">
          <stop offset="0" stop-color="var(--photo-dark-a)"/>
          <stop offset="0.45" stop-color="var(--photo-warm-a)"/>
          <stop offset="0.7" stop-color="var(--photo-warm-b)"/>
          <stop offset="1" stop-color="var(--photo-dark-b)"/>
        </linearGradient>
      </defs>
      <path d="M0,145 C60,160 150,176 200,166 C260,152 300,134 342,140 C400,149 460,165 502,182 L502,300 C440,270 350,236 270,233 C200,232 150,290 130,355 L0,355 Z" fill="url(#outsidePhoto)"/>
      <path d="M0,145 C60,160 150,176 200,166 C260,152 300,134 342,140 C400,149 460,165 502,182" fill="none" stroke="var(--accent)" stroke-width="1.2" opacity="0.7"/>
      <path d="M502,300 C440,270 350,236 270,233 C200,232 150,290 130,355" fill="none" stroke="var(--accent)" stroke-width="1.2" opacity="0.7"/>
    </svg>

    <div class="fold-line" style="left:167px"></div>
    <div class="fold-line" style="left:334px"></div>

    <h2 class="script-title about-title">About us</h2>
    <div class="body-copy about-copy">
      <p>Lorem ipsum dolor sit amet, consectetur adipiscing elit. Suspendisse consectetur justo eu nunc consequat, et blandit dolor mollis.</p>
      <p>Lorem ipsum dolor sit amet, consectetur adipiscing elit. Suspendisse consectetur justo eu nunc consequat, et blandit dolor mollis.</p>
    </div>

    <h2 class="script-title claim-title">Best Restaurant<br>in town</h2>
    <p class="body-copy claim-copy">Lorem ipsum dolor sit amet, consectetur adipiscing elit. Suspendisse consectetur justo eu nunc consequat, et blandit dolor mollis.</p>

    <div class="brand"><span class="brand-mark"></span>Malvenne</div>
    <h1 class="script-title cover-title">
      <span class="line-small">Enjoy!</span>
      <span class="line-large">Breakfast</span>
    </h1>

    <p class="website">www.malvennekitchen.com</p>
    <p class="hours">EVERYDAY<br>OPEN 7AM. 9PM</p>
  </section>

  <!-- Inside sheet: menu -->
  <section class="sheet sheet--inside">
    <div class="panel-shade panel-shade--a"></div>
    <div class="panel-shade panel-shade--b"></div>
    <div class="panel-shade panel-shade--c"></div>

    <svg class="photo-layer" viewBox="0 0 502 355" role="img" aria-label="Food photograph: stir-fried noodles in a dark pan with sauce, parsley, red pepper and sesame on a dark wooden table">
      <defs>
        <linearGradient id="insidePhoto" x1="0" y1="0" x2="1" y2="1">
          <stop offset="0" stop-color="#4a4440"/>
          <stop offset="0.35" stop-color="#3b4a2c"/>
          <stop offset="0.7" stop-color="#7a4a2a"/>
          <stop offset="1" stop-color="#2f2c2a"/>
        </linearGradient>
      </defs>
      <path d="M328,0 L502,0 L502,355 L350,355 C384,300 402,250 372,190 C346,140 334,80 328,0 Z" fill="url(#insidePhoto)"/>
      <path d="M328,0 C334,80 346,140 372,190 C402,250 384,300 350,355" fill="none" stroke="var(--accent)" stroke-width="1.2" opacity="0.7"/>
    </svg>

    <div class="fold-line" style="left:167px"></div>
    <div class="fold-line" style="left:334px"></div>

    <h2 class="script-title menu-title menu-title--foods">Foods</h2>
    <div class="menu-column menu-column--foods">
      <div class="menu-group">
        <h3>LOREM IPSUM</h3>
        <div class="menu-item"><span>Lorem ipsum dolor sit</span><span class="price">$10.-</span></div>
        <div class="menu-item"><span>Pellentesque consectetur</span><span class="price">$20.-</span></div>
        <div class="menu-item"><span>In at lorem in massa</span><span class="price">$10.-</span></div>
      </div>
      <div class="menu-group">
        <h3>LOREM IPSUM</h3>
        <div class="menu-item"><span>Lorem ipsum dolor sit</span><span class="price">$10.-</span></div>
        <div class="menu-item"><span>Pellentesque consectetur</span><span class="price">$20.-</span></div>
        <div class="menu-item"><span>In at lorem in massa</span><span class="price">$10.-</span></div>
      </div>
      <div class="menu-group">
        <h3>LOREM IPSUM</h3>
        <div class="menu-item"><span>Lorem ipsum dolor sit</span><span class="price">$10.-</span></div>
        <div class="menu-item"><span>Pellentesque consectetur</span><span class="price">$20.-</span></div>
        <div class="menu-item"><span>In at lorem in massa</span><span class="price">$10.-</span></div>
      </div>
      <div class="menu-group">
        <h3>LOREM IPSUM</h3>
        <div class="menu-item"><span>Lorem ipsum dolor sit</span><span class="price">$10.-</span></div>
        <div class="menu-item"><span>Pellentesque consectetur</span><span class="price">$20.-</span></div>
        <div class="menu-item"><span>In at lorem in massa</span><span class="price">$10.-</span></div>
      </div>
    </div>

    <h2 class="script-title menu-title menu-title--drinks">Drinks</h2>
    <div class="menu-column menu-column--drinks">
      <div class="menu-group">
        <h3>LOREM IPSUM</h3>
        <div class="menu-item"><span>Lorem ipsum dolor sit</span><span class="price">$10.-</span></div>
        <div class="menu-item"><span>Pellentesque consectetur</span><span class="price">$20.-</span></div>
        <div class="menu-item"><span>In at lorem in massa</span><span class="price">$10.-</span></div>
      </div>
      <div class="menu-group">
        <h3>LOREM IPSUM</h3>
        <div class="menu-item"><span>Lorem ipsum dolor sit</span><span class="price">$10.-</span></div>
        <div class="menu-item"><span>Pellentesque consectetur</span><span class="price">$20.-</span></div>
        <div class="menu-item"><span>In at lorem in massa</span><span class="price">$10.-</span></div>
      </div>
      <div class="menu-group">
        <h3>LOREM IPSUM</h3>
        <div class="menu-item"><span>Lorem ipsum dolor sit</span><span class="price">$10.-</span></div>
        <div class="menu-item"><span>Pellentesque consectetur</span><span class="price">$20.-</span></div>
        <div class="menu-item"><span>In at lorem in massa</span><span class="price">$10.-</span></div>
      </div>
      <div class="menu-group">
        <h3>LOREM IPSUM</h3>
        <div class="menu-item"><span>Lorem ipsum dolor sit</span><span class="price">$10.-</span></div>
        <div class="menu-item"><span>Pellentesque consectetur</span><span class="price">$20.-</span></div>
        <div class="menu-item"><span>In at lorem in massa</span><span class="price">$10.-</span></div>
      </div>
    </div>
  </section>

</main>
</body>
</html>
```